Vantor Apparel - T-Shirts on Storevia

Hi - I'm creating a new site to sell undershirts. The premise of the undershirt is that it has a U-neck shape so that your white undershirt does not show when you are wearing a button shirt. I want the site to be fun but still look stunning because I want to attract a certain clientele (business professionals with a sense of humor). I'm creating a funny video to post on the site to hopefully get some social media buzz.
I want the design to highlight the product but more importantly the lifestyle of the person who wears it. This is an undershirt so nobody really sees it and that's the point.
Since this is a single product that I want to sell, I want to make sure that the design works with Storevia. Since this is not for theme development, this design must work with an existing theme on Storevia (preferably free but if you must then no more than $75). You can choose the theme to design for.
Products:
* Single vantor undershirt in 4 sizes - S, M, L and XL
* 3 packs or 7 packs (buy 6 get 1 free)
* One-time purchase or subscription (delivery every 3 or 6 months) - I know this will require custom theme development
Attached you will find a very rough idea for the site and this was made before I had considered putting in a video (Brix template). It's going to be tough to catch lightning in a bottle much like Penny Razor Guild but that's what I'm hoping for.
Name of the company is Vantor Apparel. Logo attached. Included .ai file which has some funky colors so please use the light blue color logo similar to the png's attached.
Here is the site for a competitor. There's much to be improved on the site but I include it here because the concept of the undershirt is the same: http://www.mirelgarments.example
Feel free to use stock images that I can purchase on the site that represents a young and cool vibe. I will be taking shots of the shirts for the product page so for now use some generic shirt please.
Updates
Project Deadline Extended
Reason: Please take a look at feedback for other designs. I'm hoping for my mockup to be an inspiration, not just re-skinning the mockup I created. Plus it must be based on a Storevia theme. Use stock images as necessary but keep the budget for purchasing images under $100.
Target Market(s)
Male 30-50

```html
<!DOCTYPE html>
<html lang="en">
<head>
<meta charset="utf-8">
<title>Vantor Apparel</title>
<link href="https://fonts.googleapis.com/css2?family=Roboto:wght@400;500;700;900&display=swap" rel="stylesheet">
<style>
:root{
  --page:#f0f0f0;
  --white:#ffffff;
  --ink:#1e1e1e;
  --muted:#555555;
  --line:#e3e3e3;
  --black:#0b0b0b;
  --red:#e53935;
  --blue:#2aa3dc;
  --navy:#1d3550;
  --footer:#262626;
  --footer-text:#bdbdbd;
  --cotton:#fbfbfb;
  --cotton-shade:#d9d9d9;
}
*{box-sizing:border-box;margin:0;padding:0}
html,body{width:1200px;height:2672px;overflow:hidden}
body{position:relative;background:var(--page);font-family:"Roboto",Arial,sans-serif;color:var(--ink)}
.abs{position:absolute}
.panel{position:absolute;background:var(--white)}
.btn-outline{display:inline-block;border:2px solid #333;font-size:12px;font-weight:500;letter-spacing:.5px;padding:8px 16px;background:var(--white);color:var(--ink)}
.price{color:var(--red);font-weight:700;font-size:15px}
.price span{margin:0 8px}
.small{font-size:10px;line-height:13px;color:#333}
.small b{color:var(--blue);font-weight:500}
.heading{font-size:17px;font-weight:700;letter-spacing:.4px}
.arrows{position:absolute;display:flex;gap:6px}
.arrows i{width:24px;height:24px;background:#e8e8e8;display:flex;align-items:center;justify-content:center;font-style:normal;font-size:13px;color:#666}

/* product photo areas: soft white cotton tones on white */
.shirt{position:absolute;background:
  radial-gradient(ellipse 60% 14% at 50% 96%,rgba(0,0,0,.16),rgba(0,0,0,0) 100%),
  radial-gradient(ellipse 55% 48% at 42% 40%,#ffffff 0%,#f6f6f6 45%,rgba(230,230,230,.9) 75%,rgba(255,255,255,0) 100%),
  radial-gradient(ellipse 40% 38% at 64% 66%,#f2f2f2 0%,rgba(214,214,214,.85) 60%,rgba(255,255,255,0) 100%);
}
.badge{position:absolute;color:#fff;font-size:10px;font-weight:700;padding:4px 10px;z-index:1}
.badge.red{background:var(--red)}
.badge.blue{background:var(--blue)}

/* top bar */
.topbar{left:0;top:0;width:1200px;height:40px;background:var(--black);color:#fff;font-size:12px}
.topbar .welcome{left:94px;top:13px}
.topbar .tools{right:94px;top:13px;display:flex;gap:26px}
/* header */
.header{left:0;top:40px;width:1200px;height:90px;background:var(--white)}
.logo{left:94px;top:20px;font-size:36px;font-weight:700;color:var(--ink);display:flex;align-items:center;gap:10px}
.logo .mark{width:14px;height:14px;background:var(--blue)}
.nav{right:94px;top:38px;display:flex;gap:32px;font-size:13px;font-weight:700;align-items:center}
/* hero */
.hero-photo{left:94px;top:156px;width:578px;height:356px;background:
  radial-gradient(ellipse 30% 55% at 30% 75%,#d9e6f1 0%,#b4cde0 50%,rgba(180,205,224,0) 100%),
  radial-gradient(ellipse 28% 50% at 62% 82%,#e6eef5 0%,#c3d4e3 55%,rgba(195,212,227,0) 100%),
  radial-gradient(ellipse 14% 18% at 36% 30%,#e2b99a 0%,rgba(226,185,154,0) 100%),
  radial-gradient(ellipse 14% 18% at 58% 40%,#e8c4a6 0%,rgba(232,196,166,0) 100%),
  linear-gradient(100deg,#4f6c86 0%,#6f8aa3 45%,#5d7892 100%)}
.hero-copy{left:672px;top:156px;width:434px;height:356px;background:linear-gradient(90deg,#1a1a1a,#000 60%,#111);color:#fff;text-align:center}
.hero-copy h1{margin-top:70px;font-size:31px;font-weight:700;letter-spacing:1px}
.hero-copy hr{width:270px;margin:18px auto 20px;border:0;border-top:2px solid #bbb}
.hero-copy p{font-size:12px;line-height:21px;width:300px;margin:0 auto}
.hero-copy .view{display:inline-block;margin-top:38px;border:2px solid #fff;padding:8px 12px;font-size:12px;font-weight:700}

/* category */
.category{left:94px;top:539px;width:231px;height:307px}
.category .heading{position:absolute;left:13px;top:20px}
.category ul{position:absolute;left:13px;top:58px;width:205px;list-style:none;font-size:10px;color:#333}
.category li{height:36px;line-height:18px;border-bottom:1px solid var(--line)}
.category li:last-child{border:0}

/* promo */
.promo{left:352px;top:539px;width:754px;height:269px}
.promo .tag{position:absolute;left:26px;top:10px;background:var(--blue);color:#fff;font-weight:700;font-size:15px;padding:15px 14px;letter-spacing:.5px}
.promo h3{position:absolute;left:44px;top:76px;font-size:16px;font-weight:700}
.promo .price{position:absolute;left:44px;top:112px;font-size:17px}
.promo .small{position:absolute;left:44px;top:142px;width:210px}
.promo .btn-outline{position:absolute;left:44px;top:206px}
.promo .model{background:
  radial-gradient(ellipse 46% 40% at 50% 52%,#ffffff 0%,#f7f7f7 55%,rgba(225,225,225,0) 100%),
  radial-gradient(ellipse 16% 14% at 50% 10%,#d9a98a 0%,rgba(217,169,138,0) 100%),
  radial-gradient(ellipse 22% 20% at 22% 60%,#dcae90 0%,rgba(220,174,144,0) 100%),
  radial-gradient(ellipse 22% 20% at 78% 60%,#dcae90 0%,rgba(220,174,144,0) 100%),
  linear-gradient(180deg,#ffffff,#ffffff)}

/* product grids */
.grid{position:absolute;display:flex}
.card{width:251px;position:relative;text-align:center}
.card .name{font-size:11px;font-weight:700}
.card .price{margin-top:14px;font-size:14px}
.card .small{margin-top:8px}
.card .btn-outline{margin-top:10px;padding:7px 14px;font-size:11px}

.newproduct{left:352px;top:837px;width:754px;height:421px}
.featured{left:352px;top:1305px;width:754px;height:443px}

/* best seller */
.best{left:94px;top:886px;width:231px;height:390px}
.best .heading{position:absolute;left:13px;top:20px}
.best-item{position:absolute;left:13px;width:210px;height:70px}
.best-item .shirt{left:0;top:0;width:62px;height:64px}
.best-item .name{position:absolute;left:80px;top:8px;font-size:10px;font-weight:700}
.best-item .rule{position:absolute;left:80px;top:24px;width:46px;height:2px;background:var(--blue)}
.best-item .price{position:absolute;left:80px;top:40px;font-size:13px}

/* special */
.special{left:94px;top:1305px;width:231px;height:438px;text-align:center}
.special .heading{position:absolute;left:13px;top:22px}

.viewmore{left:352px;top:1748px;width:754px;height:37px;background:var(--black);color:#fff;font-size:11px;font-weight:700;text-align:center;line-height:37px}

/* testimonials */
.customers{left:94px;top:1785px;width:231px;height:152px}
.customers .heading{position:absolute;left:13px;top:22px}
.customers .who{position:absolute;left:24px;top:58px;font-size:12px;font-weight:700}
.customers .rule{position:absolute;left:24px;top:76px;width:80px;height:2px;background:var(--blue)}
.customers .small{position:absolute;left:24px;top:88px;width:190px;font-size:9px;line-height:12px}

/* subscription banner */
.banner{left:352px;top:1814px;width:754px;height:123px;background:linear-gradient(90deg,#bfe1f2,#e6f3fa 60%,#d6ebf6);overflow:hidden}
.banner .photo{position:absolute;left:0;top:0;width:200px;height:123px;background:
  radial-gradient(ellipse 30% 45% at 35% 40%,#3a3f48 0%,rgba(58,63,72,0) 100%),
  radial-gradient(ellipse 40% 50% at 45% 85%,#f4f6f8 0%,rgba(244,246,248,0) 100%),
  radial-gradient(ellipse 22% 30% at 60% 45%,#d8a98a 0%,rgba(216,169,138,0) 100%),
  linear-gradient(90deg,#a9c9dc,#d3e8f3 80%,rgba(211,232,243,0))}
.banner h2{position:absolute;left:206px;top:22px;font-size:22px;line-height:28px;font-weight:700;color:var(--navy);letter-spacing:.6px}
.banner p{position:absolute;left:206px;top:82px;font-size:17px;color:var(--navy)}
.banner .side{position:absolute;right:0;top:0;width:224px;height:123px;background:linear-gradient(90deg,#1d2a38,#2b3c4e)}
.banner .shop{position:absolute;left:40px;top:48px;display:flex;border:2px solid #fff}
.banner .shop span{background:#fff;color:var(--ink);font-size:12px;font-weight:700;padding:8px 14px}
.banner .shop i{width:30px;display:flex;align-items:center;justify-content:center}

/* lower */
.lower{left:94px;top:1966px;width:1012px;height:356px}
.lower .heading{font-size:16px}
.blog{position:absolute;left:13px;top:0;width:300px}
.blog .heading{position:absolute;top:22px}
.post{position:absolute;left:0;width:300px}
.post h4{font-size:10px;font-weight:700}
.post .date{font-size:9px;color:#666;margin-top:8px}
.post .small{margin-top:8px;font-size:8.5px;line-height:12px}
.post .more{font-size:9px;margin-top:20px}
.blog .divider{position:absolute;left:0;top:192px;width:300px;height:1px;background:var(--line)}
.tweets{position:absolute;left:340px;top:0;width:310px}
.tweets .heading{position:absolute;left:4px;top:22px}
.tweet{position:absolute;left:16px;width:300px;height:70px}
.tweet .bubble{position:absolute;left:0;top:10px;width:42px;height:42px;border-radius:50%;background:var(--blue)}
.tweet .body{position:absolute;left:80px;top:0;width:220px;font-size:8.5px;line-height:12px}
.tweet .body b{color:var(--ink)}
.tweet .body em{color:var(--blue);font-style:normal}
.tweet .via{margin-top:8px;font-size:8px}
.video{position:absolute;left:688px;top:0;width:316px}
.video .heading{position:absolute;left:0;top:22px}
.video .frame{position:absolute;left:0;top:54px;width:310px;height:284px;background:
  radial-gradient(ellipse 26% 40% at 48% 52%,#a8acae 0%,rgba(168,172,174,0) 100%),
  radial-gradient(ellipse 20% 20% at 46% 16%,#b88a6c 0%,rgba(184,138,108,0) 100%),
  radial-gradient(ellipse 30% 18% at 48% 94%,#5d7593 0%,rgba(93,117,147,0) 100%),
  linear-gradient(120deg,#7d7b78,#b9b6b1 45%,#6d6b68)}
.video .play{position:absolute;left:124px;top:111px;width:62px;height:62px;border-radius:50%;background:rgba(255,255,255,.85);display:flex;align-items:center;justify-content:center}
.spacer{left:94px;top:2344px;width:1012px;height:38px}

/* footer */
.footer{left:0;top:2382px;width:1200px;height:222px;background:var(--footer);color:#fff}
.fcol{position:absolute;top:44px}
.fcol h5{font-size:12px;font-weight:700;margin-bottom:14px}
.fcol ul{list-style:none;font-size:10px;color:var(--footer-text);line-height:22px}
.fcol p{font-size:10px;color:var(--footer-text);width:300px}
.subscribe{display:flex;margin-top:34px}
.subscribe span{width:178px;height:28px;background:var(--footer);border:1px solid #888;color:#aaa;font-size:9px;text-align:center;line-height:26px}
.subscribe b{width:70px;height:28px;background:#fff;color:var(--ink);font-size:10px;text-align:center;line-height:28px}
.socials{display:flex;gap:8px}
.socials i{width:20px;height:20px;border-radius:50%;background:#fff}
.cards{display:flex;gap:6px;margin-top:12px}
.cards i{width:26px;height:14px;background:#e8e8e8;border-radius:2px}
.bottom{left:0;top:2604px;width:1200px;height:68px;background:var(--black);color:#fff;font-size:11px}
.bottom .copy{position:absolute;left:94px;top:28px}
.bottom .links{position:absolute;right:94px;top:28px;display:flex;gap:22px}
</style>
</head>
<body>

<div class="abs topbar">
  <div class="abs welcome">Welcome to our online store! Login or Signup</div>
  <div class="abs tools"><span>&#9881; Setting &#709;</span><span>&#9679; My Account &#709;</span><span>&#128722; Cart: 0 item</span></div>
</div>

<header class="abs header">
  <div class="abs logo"><span>vantor Apparel</span><span class="mark"></span></div>
  <nav class="abs nav">
    <span>HOME</span><span>CATEGORIES</span><span>ABOUT US</span><span>FAQs</span><span>CONTACT US</span>
    <svg width="14" height="14" viewBox="0 0 14 14"><circle cx="6" cy="6" r="4.5" fill="none" stroke="#222" stroke-width="1.8"/><line x1="9.5" y1="9.5" x2="13" y2="13" stroke="#222" stroke-width="1.8"/></svg>
  </nav>
</header>

<div class="abs hero-photo" role="img" aria-label="Smiling couple in light blue shirts against a blue wall"></div>
<div class="abs hero-copy">
  <h1>LOREM IPSUMEI</h1>
  <hr>
  <p>aspernatur magni quae aperiam aut veritatis beatae eos aut voluptas doloremque perspiciatis error natus natus aut eaque inventore quasi consequuntur consequuntur ipsa aspernatur iste sit</p>
  <span class="view">VIEW MORE</span>
</div>

<aside class="panel category">
  <div class="heading">SHOP BY CATEGORY</div>
  <ul>
    <li>SINGLE VANTOR UNDERSHIRT <b>S</b></li>
    <li>SINGLE VANTOR UNDERSHIRT <b>M</b></li>
    <li>SINGLE VANTOR UNDERSHIRT <b>L</b></li>
    <li>SINGLE VANTOR UNDERSHIRT <b>XL</b></li>
    <li>3 PACKS</li>
    <li>7 PACKS</li>
    <li>ONE-TIME PURCHASE</li>
  </ul>
</aside>

<section class="panel promo">
  <div class="tag">BUY 6 GET 1 FREE</div>
  <h3>VANTOR UNDERSHIRT 707</h3>
  <div class="price">$44.00<span>-</span>$24.00</div>
  <p class="small">ipsum dolor sit amet voluptatem fugit aut illo inventore aut quasi <b>every six months</b> or <b>only single item</b></p>
  <span class="btn-outline">ADD TO CART</span>
  <div class="shirt" style="left:290px;top:44px;width:126px;height:156px" role="img" aria-label="Stack of white undershirts"></div>
  <div class="abs model" style="left:485px;top:30px;width:190px;height:222px" role="img" aria-label="Man wearing a white V-neck undershirt"></div>
</section>

<section class="panel newproduct">
  <div class="heading abs" style="left:13px;top:25px">NEW PRODUCT</div>
  <div class="arrows" style="right:16px;top:18px"><i>&#8249;</i><i>&#8250;</i></div>
  <div class="grid" style="left:0;top:63px">
    <div class="card"><span class="badge red" style="left:26px;top:0">NEW</span><div class="shirt" style="left:50px;top:16px;width:156px;height:150px" role="img" aria-label="Three folded white undershirts"></div><div style="height:200px"></div><div class="name">VANTOR UNDERSHIRT 01</div><div class="price">$30.00<span>-</span>$11.00</div><p class="small">ipsum dolor sit amet voluptatem fugit aut illo<br><b>every six months or only single item</b></p><span class="btn-outline">ADD TO CART</span></div>
    <div class="card"><span class="badge blue" style="left:26px;top:0">70%</span><div class="shirt" style="left:40px;top:10px;width:176px;height:160px" role="img" aria-label="Pack of white undershirts"></div><div style="height:200px"></div><div class="name">VANTOR UNDERSHIRT 02</div><div class="price">$30.00<span>-</span>$11.00</div><p class="small">ipsum dolor sit amet voluptatem fugit aut illo<br><b>every six months or only single item</b></p><span class="btn-outline">ADD TO CART</span></div>
    <div class="card"><span class="badge red" style="left:26px;top:0">NEW</span><div class="shirt" style="left:54px;top:14px;width:150px;height:156px" role="img" aria-label="White undershirt with folded pack"></div><div style="height:200px"></div><div class="name">VANTOR UNDERSHIRT 03</div><div class="price">$30.00<span>-</span>$11.00</div><p class="small">ipsum dolor sit amet voluptatem fugit aut illo<br><b>every six months or only single item</b></p><span class="btn-outline">ADD TO CART</span></div>
  </div>
</section>

<aside class="panel best">
  <div class="heading">BEST SELLER</div>
  <div class="best-item" style="top:62px"><div class="shirt" role="img" aria-label="White undershirt pack"></div><div class="name">VANTOR UNDERSHIRT 01</div><div class="rule"></div><div class="price">$30.00<span>-</span>$11.00</div></div>
  <div class="best-item" style="top:142px"><div class="shirt" role="img" aria-label="White undershirt pack"></div><div class="name">VANTOR UNDERSHIRT 01</div><div class="rule"></div><div class="price">$30.00<span>-</span>$11.00</div></div>
  <div class="best-item" style="top:222px"><div class="shirt" role="img" aria-label="White undershirt pack"></div><div class="name">VANTOR UNDERSHIRT 01</div><div class="rule"></div><div class="price">$30.00<span>-</span>$11.00</div></div>
  <div class="best-item" style="top:308px"><div class="shirt" role="img" aria-label="White undershirt"></div><div class="name">VANTOR UNDERSHIRT 01</div><div class="rule"></div><div class="price">$30.00<span>-</span>$11.00</div></div>
</aside>

<aside class="panel special">
  <div class="heading">SPECIAL OFFER</div>
  <div class="arrows" style="right:16px;top:17px"><i>&#8249;</i><i>&#8250;</i></div>
  <div class="shirt" style="left:26px;top:62px;width:180px;height:200px" role="img" aria-label="White undershirt above a stack of folded shirts"></div>
  <div class="abs" style="left:0;top:268px;width:231px">
    <div style="font-size:11px;font-weight:700">VANTOR UNDERSHIRT 04</div>
    <div style="width:40px;height:2px;background:var(--blue);margin:8px auto 0"></div>
    <p class="small" style="margin-top:26px;font-size:9px">ipsum dolor sit amet voluptatem fugit aut illo<br><b>every six months or only single item</b></p>
    <span class="btn-outline" style="margin-top:12px;padding:7px 14px;font-size:11px">ADD TO CART</span>
  </div>
</aside>

<section class="panel featured">
  <div class="heading abs" style="left:20px;top:30px">FEATURED PRODUCTS</div>
  <div class="grid" style="left:0;top:72px">
    <div class="card"><span class="badge red" style="left:26px;top:0">NEW</span><div class="shirt" style="left:46px;top:14px;width:164px;height:160px" role="img" aria-label="Folded white undershirts"></div><div style="height:200px"></div><div class="name">VANTOR UNDERSHIRT 04</div><div class="price">$30.00<span>-</span>$11.00</div><p class="small">ipsum dolor sit amet voluptatem fugit aut illo<br><b>every six months or only single item</b></p><span class="btn-outline">ADD TO CART</span></div>
    <div class="card"><div class="shirt" style="left:46px;top:14px;width:164px;height:160px" role="img" aria-label="Folded white undershirts"></div><div style="height:200px"></div><div class="name">VANTOR UNDERSHIRT 05</div><div class="price">$30.00<span>-</span>$11.00</div><p class="small">ipsum dolor sit amet voluptatem fugit aut illo<br><b>every six months or only single item</b></p><span class="btn-outline">ADD TO CART</span></div>
    <div class="card"><span class="badge red" style="left:26px;top:0">NEW</span><div class="shirt" style="left:52px;top:14px;width:154px;height:160px" role="img" aria-label="White undershirt with folded pack"></div><div style="height:200px"></div><div class="name">VANTOR UNDERSHIRT 06</div><div class="price">$30.00<span>-</span>$11.00</div><p class="small">ipsum dolor sit amet voluptatem fugit aut illo<br><b>every six months or only single item</b></p><span class="btn-outline">ADD TO CART</span></div>
  </div>
</section>
<div class="abs viewmore">VIEW MORE ITEMS</div>

<aside class="panel customers">
  <div class="heading">CUSTOMERS SAY</div>
  <div class="who">JOHN DOE</div>
  <div class="rule"></div>
  <p class="small">Lorem ipsum dolor sit amet voluptatem fugit aut illo omnis Ut ipsum quasi illo dolores voluptatem doloremque perspiciatis beatae magni</p>
</aside>

<section class="abs banner">
  <div class="photo" role="img" aria-label="Relaxed couple in casual white clothing"></div>
  <h2>ONE - TIME PURCHASE<br>OR SUBSCRIPTION</h2>
  <p>Delivery Every 3 Or 6 Months</p>
  <div class="side">
    <div class="shop"><span>SHOP NOW</span><i><svg width="16" height="14" viewBox="0 0 16 14"><path d="M1 1h3l2 8h8l1.5-6H5" fill="none" stroke="#fff" stroke-width="1.6"/><circle cx="7" cy="12" r="1.3" fill="#fff"/><circle cx="13" cy="12" r="1.3" fill="#fff"/></svg></i></div>
  </div>
</section>

<section class="panel lower">
  <div class="blog">
    <div class="heading">LATES FROM BLOG</div>
    <div class="arrows" style="left:246px;top:16px"><i>&#8249;</i><i>&#8250;</i></div>
    <div class="post" style="top:62px">
      <h4>LOREM IPSUM DOLOR SIT AMET REM EOS</h4>
      <div class="date">May 18, 2014</div>
      <p class="small">Lorem ipsum dolor sit amet voluptatem fugit aut illo omnis rem ipsa quasi illo dolores voluptatem doloremque perspiciatis beatae magni architecto sunt odit, aspernatur magni quae aperiam aut eos aut voluptas quasi consequuntur consequuntur ipsa</p>
      <div class="more">read more</div>
    </div>
    <div class="divider"></div>
    <div class="post" style="top:210px">
      <h4>LOREM IPSUM DOLOR SIT AMET REM EOS</h4>
      <div class="date">May 18, 2014</div>
      <p class="small">Lorem ipsum dolor sit amet voluptatem fugit aut illo omnis rem ipsa quasi illo dolores voluptatem doloremque perspiciatis beatae magni architecto sunt odit, aspernatur magni quae aperiam aut eos aut voluptas quasi consequuntur consequuntur ipsa</p>
      <div class="more">read more</div>
    </div>
  </div>
  <div class="tweets">
    <div class="heading">TWEETS</div>
    <div class="tweet" style="top:62px"><div class="bubble"></div><div class="body"><b>John Doe</b> <em>@Orla Venn</em><br>Lorem ipsum dolor sit amet voluptatem fugit aut illo omnis explicabo ipsa rerum rem ipsam<div class="via">retweeted by <b>Media Doe</b></div></div></div>
    <div class="tweet" style="top:162px"><div class="bubble"></div><div class="body"><b>John Doe</b> <em>@Orla Venn</em><br>Lorem ipsum dolor sit amet voluptatem fugit aut illo omnis explicabo ipsa rerum rem ipsam<div class="via">retweeted by <b>Media Doe</b></div></div></div>
    <div class="tweet" style="top:256px"><div class="bubble"></div><div class="body"><b>John Doe</b> <em>@Orla Venn</em><br>Lorem ipsum dolor sit amet voluptatem fugit aut illo omnis explicabo ipsa rerum rem ipsam<div class="via">retweeted by <b>Media Doe</b></div></div></div>
  </div>
  <div class="video">
    <div class="heading">WATCH OUR VIDEO</div>
    <div class="frame" role="img" aria-label="Video still of a man in a grey undershirt and jeans against a concrete wall">
      <div class="play"><svg width="22" height="26" viewBox="0 0 22 26"><path d="M2 1l19 12L2 25z" fill="#555"/></svg></div>
    </div>
  </div>
</section>
<div class="panel spacer"></div>

<footer class="abs footer">
  <div class="fcol" style="left:94px"><h5>COMPANY</h5><ul><li>Search</li><li>About</li><li>News</li><li>Retailers</li><li>Contact Us</li></ul></div>
  <div class="fcol" style="left:265px"><h5>SHIPPING</h5><ul><li>Shipping Fee</li><li>Order and Returns</li><li>Track Order</li><li>Search Term</li><li>Site Map</li></ul></div>
  <div class="fcol" style="left:442px"><h5>FAQs</h5><ul><li>Customers Service</li><li>Privacy Policy</li><li>Term and Use</li><li>My Account</li><li>Others</li></ul></div>
  <div class="fcol" style="left:612px"><h5>NEWS &amp; UPDATES</h5><p>Sign up to get the latest on sales, new releases and more ...</p><div class="subscribe"><span>enter your email here</span><b>SIGN UP</b></div></div>
  <div class="fcol" style="left:960px"><h5>FOLLOW US NOW</h5><div class="socials"><i></i><i></i><i></i><i></i><i></i></div>
    <h5 style="margin-top:22px;border-top:1px solid #555;padding-top:12px;width:128px">PAYMENT METHOD</h5><div class="cards" style="margin-top:0"><i></i><i></i><i></i><i></i><i></i></div></div>
</footer>
<div class="abs bottom">
  <div class="copy">&copy; 2014 <b>Your Company</b></div>
  <div class="links"><span>About us</span><span>privacy policy</span><span>terms and use</span><span>Careers</span><span>Countries</span><span>contact us</span></div>
</div>

</body>
</html>
```